Unique Banner Design for weight loss project

We need a banner set for an online coaching program for weight loss. The following sizes are needed:
400x400
180x150
200x600
120x600
160x600
468x60
728x90
336x280
234x60
250x250
300x250
125x125

Here is the text:

1 verbotenes Lebensmittel, das du niemals essen darfst.

subhead: Verliere täglich etwas Bauchfett, indem du dieses 1 alltägliche Lebensmittel meidest.

***important: The Banner and image should be looked "hand drawn" LIKE the examples. For the image please DONT USE A BANANA. you can use one of the following veggies/fruits (of course hand drawn like the examples):

-cucumber
-potato
-Corncob
-zucchini
Updates

Reason: Wir haben bereits einen Sieger für unser Projekt. Dieser sollte lediglich noch 1-2 kleine Änderungen am Design vornehmen, dann wird der Designer ausgewählt.

Target Market(s)

weight loss, diet, nutrition

Industry/Entity Type

Weight

Requirements
Must have
• Here is the text:
• 1 verbotenes Lebensmittel, das du niemals essen darfst.
• subhead: Verliere täglich etwas Bauchfett, indem du dieses 1 alltägliche Lebensmittel meidest.
• ***important: The Banner and image should be looked "hand drawn" LIKE the examples. For the image please DONT USE A BANANA. you can use one of the following veggies/fruits (of course hand drawn like the examples):
• -cucumber
• -potato
• -Corncob
• -zucchini
Nice to have
• animated banner like "someone is eating the food" (see one of the examples)
Should not have
• NO strong call to action like click here or anyone else!

```html
<!DOCTYPE html>
<html lang="de">
<head>
<meta charset="utf-8">
<title>Banner-Set: 1 verbotenes Lebensmittel</title>
<link rel="stylesheet" href="https://fonts.googleapis.com/css2?family=Amatic+SC:wght@700&family=Roboto+Condensed:ital,wght@1,400&display=swap">
<style>
  :root {
    --backdrop: #1d1d1d;
    --paper: #ffffff;
    --brown: #8f5d1d;
    --brown-text: #9b6520;
    --ink: #474747;
    --frame: #d4d4d4;
    --art-top: #f7ecd6;
    --art-bottom: #efd9ac;
  }
  * { box-sizing: border-box; margin: 0; padding: 0; }
  html, body { width: 1200px; height: 1200px; overflow: hidden; }
  body { background: var(--backdrop); position: relative; }

  .banner {
    position: absolute;
    width: 467px;
    height: 389px;
    background: var(--paper);
    display: flex;
    flex-direction: column;
    overflow: hidden;
  }
  .banner--header-band { left: 124px; top: 232px; }
  .banner--footer-band { left: 644px; top: 232px; }
  .banner--framed { left: 367px; top: 703px; border: 4px solid var(--frame); }

  .headline {
    font-family: "Amatic SC", cursive;
    font-weight: 700;
    font-size: 47px;
    line-height: 45px;
    text-align: center;
    padding: 10px 10px 0;
    flex: none;
  }
  .banner--header-band .headline {
    background: var(--brown);
    color: var(--paper);
    height: 117px;
    padding-top: 13px;
  }
  .banner--footer-band .headline { color: var(--ink); height: 108px; }
  .banner--framed .headline { color: var(--brown-text); height: 104px; }

  .food-illustration {
    flex: 1;
    margin: 4px 60px 0;
    background: linear-gradient(180deg, var(--art-top), var(--art-bottom));
  }

  .subhead {
    font-family: "Roboto Condensed", sans-serif;
    font-style: italic;
    font-weight: 400;
    font-size: 22px;
    line-height: 23px;
    text-align: center;
    color: var(--ink);
    height: 64px;
    padding-top: 7px;
    flex: none;
    white-space: nowrap;
  }
  .banner--footer-band .subhead {
    background: var(--brown);
    color: var(--paper);
    margin-top: 6px;
    padding-top: 9px;
  }
</style>
</head>
<body>
  <section class="banner banner--header-band">
    <h1 class="headline">1 verbotenes Lebensmittel,<br>das du niemals essen darfst</h1>
    <div class="food-illustration" role="img" aria-label="Handgezeichnete Kartoffel"></div>
    <p class="subhead">Verliere täglich etwas Bauchfett, indem<br>du dieses 1 alltägliche Lebensmittel meidest</p>
  </section>

  <section class="banner banner--footer-band">
    <h1 class="headline">1 verbotenes Lebensmittel,<br>das du niemals essen darfst</h1>
    <div class="food-illustration" role="img" aria-label="Handgezeichnete Kartoffel"></div>
    <p class="subhead">Verliere täglich etwas Bauchfett, indem<br>du dieses 1 alltägliche Lebensmittel meidest</p>
  </section>

  <section class="banner banner--framed">
    <h1 class="headline">1 verbotenes Lebensmittel,<br>das du niemals essen darfst</h1>
    <div class="food-illustration" role="img" aria-label="Handgezeichnete Kartoffel"></div>
    <p class="subhead">Verliere täglich etwas Bauchfett, indem<br>du dieses 1 alltägliche Lebensmittel meidest</p>
  </section>
</body>
</html>
```